Norvane Freight and Provision Service Brochure

Please see http://www.norvanefreight.example for who we are and what we do.
We would like to see a design that matches the industry we work in i.e. Oil and Gas. The design should communicate large, heavy field operations, supply of vast bulk fuel quantities to our US and Afghan Military customers, plus financial independence and the companies whatever it takes attitude operation in remote often hostile areas. Dark colors like on the website - contrasting our green logo. A strong focus on our past performance/past experience.

Target Market(s)

Military Customers, Partners, Subcontractors

Industry/Entity Type

Industry

Contact Information for Business Card

Display of Address, Phone, email etc. of our 4 offices

Font styles to use
Sans Serif

Requirements
Must have
• Glossy brochure, modern, cool design. Great display (map) of our offices in the Middle East, Europe and Central Asia. A focus on our past performance/past experience. Customer logos/references
Nice to have
• Prominent highlighted watermark logo
Should not have
• Standard A4/Letter brochure

```html
<!DOCTYPE html>
<html lang="en">
<head>
<meta charset="utf-8">
<title>Norvane Freight and Provision – What We Offer</title>
<link rel="stylesheet" href="https://fonts.googleapis.com/css2?family=Montserrat:wght@500;600&family=Questrial&display=swap">
<style>
  :root {
    --backdrop: #d8d4cf;
    --page-slate: #4b5458;
    --page-slate-right: #50595c;
    --band-blue: rgba(34, 78, 118, 0.82);
    --band-blue-solid: #24507a;
    --accent-yellow: #f2e21b;
    --text-white: #ffffff;
    --text-soft: #eceff1;
  }
  * { box-sizing: border-box; margin: 0; padding: 0; }
  html, body { width: 1200px; height: 579px; overflow: hidden; background: var(--backdrop); }
  body { position: relative; font-family: "Questrial", Arial, sans-serif; color: var(--text-white); }

  .spread { position: absolute; left: 27px; top: 52px; width: 1143px; height: 463px; display: flex; }
  .page { position: relative; width: 50%; height: 100%; overflow: hidden; }
  .page--left { background: var(--page-slate); }
  .page--right { background: var(--page-slate-right); }

  .photo { position: absolute; }
  .photo--tanker-train { left: 0; top: 0; width: 100%; height: 134px;
    background: linear-gradient(100deg, #16191c 0%, #2f353b 25%, #5d656b 50%, #8f979c 72%, #c3c7c8 100%); }
  .photo--offshore-rig { left: 0; top: 261px; width: 100%; height: 202px;
    background: linear-gradient(180deg, #34495a 0%, #52687a 30%, #9a8467 55%, #b08f63 62%, #4a3b2c 76%, #1f1f20 100%); }

  .thumb { position: absolute; width: 127px; }
  .thumb--trucks { left: 26px; top: 279px; height: 72px; background: linear-gradient(135deg, #8a2c23, #4b4d52 50%, #c7c9cc); }
  .thumb--storage { left: 26px; top: 369px; height: 75px; background: linear-gradient(180deg, #3f74c6 0%, #8fb1df 45%, #e7e9ea 60%, #bfc3c5 100%); }
  .thumb--fuelling { left: 11px; top: 44px; height: 74px; background: linear-gradient(180deg, #d9e4ea 0%, #c7d3dc 50%, #2b4d9a 70%, #8d9296 100%); }
  .thumb--laboratory { left: 11px; top: 158px; height: 75px; background: linear-gradient(90deg, #6e5a24 0%, #d7b534 35%, #a8892c 65%, #4a3d1e 100%); }

  .offer-band { position: absolute; left: 0; width: 100%; }
  .page--left .offer-band { top: 134px; height: 73px; padding: 14px 0 0 22px; background: var(--band-blue-solid); }
  .page--right .offer-band { top: 261px; height: 73px; padding: 16px 0 0 17px; background: var(--band-blue); }
  .offer-band__title { font-family: "Montserrat", Arial, sans-serif; font-weight: 500; font-size: 21px; line-height: 25px; }
  .offer-band__subtitle { font-family: "Montserrat", Arial, sans-serif; font-weight: 500; font-size: 16.5px; color: var(--accent-yellow); line-height: 22px; padding-left: 4px; }

  .intro { position: absolute; left: 23px; top: 211px; width: 535px; font-size: 12px; line-height: 14.8px; }

  .service { position: absolute; }
  .service__heading { font-family: "Montserrat", Arial, sans-serif; font-weight: 600; font-size: 10.4px; color: var(--accent-yellow); line-height: 12px; margin-bottom: 1px; }
  .service__body { font-size: 7px; line-height: 8.1px; color: var(--text-soft); text-align: justify; }

  .service--land { left: 160px; top: 263px; width: 400px; }
  .service--storage { left: 160px; top: 369px; width: 400px; }
  .service--fuelling { left: 146px; top: 43px; width: 386px; }
  .service--laboratory { left: 146px; top: 170px; width: 386px; }
</style>
</head>
<body>
  <main class="spread">
    <section class="page page--left">
      <div class="photo photo--tanker-train" role="img" aria-label="Long row of rail fuel tanker cars along a track"></div>
      <header class="offer-band">
        <h1 class="offer-band__title">WHAT WE OFFER</h1>
        <h2 class="offer-band__subtitle">Fuel Distribution Logistics &amp; Services</h2>
      </header>
      <p class="intro">By truly understanding the regions in which we work in, our Operations and Fuel Distribution Logistics Teams design implement and operate complex, fuel distribution networks allowing us to offer our customers full turn-key services, all the way from the pipeline to the gas tank.</p>

      <div class="thumb thumb--trucks" role="img" aria-label="Mechanics servicing fuel truck engines in a workshop"></div>
      <article class="service service--land">
        <h3 class="service__heading">Reliable Land Fuel Distribution Logistics</h3>
        <p class="service__body">Since its founding Norvane has grown its fleet to more than 850 fuel-tanker trucks. Unlike most other companies Norvane owns the vehicle directly and operates them with its own highly trained driver personnel resulting in fast and direct access to information in the daily operations. Our strict preventative maintenance program allows us to compete as a leader in the industry with regards to dependability and professionalism. Norvane' in house maintenance facilities are company owned and operated, servicing hundreds of trucks from anything from minor maintenance such as air/fuel filters to major mechanical overhauls of engines and transmissions for any older asset in need of upgrade. In addition to our own fuel trucking capabilities and reliable supply at competitive fuel prices, we provide local market expertise in our network of leading regional companies, and a full spectrum of land fuel products, fuel services and fuel logistics solutions.</p>
      </article>

      <div class="thumb thumb--storage" role="img" aria-label="White fuel storage tanks against a blue sky"></div>
      <article class="service service--storage">
        <h3 class="service__heading">State of the art Fuel Storage Facilities</h3>
        <p class="service__body">Norvane' strategic, intermediate or destination fuel storage facilities are strategically located at border crossings at the main entry/border crossing points for bulk fuel along the various supply chains corridors. Our other main storage capacities in capital cities enable us to minimise the risk of disruption and to meet our customers' requirements for one time delivery and fuel storage needs. Most of these facilities are company owned and operated, while others are leased from the commercial market. For any solution, we ensure that the operations of the storage facility are in accordance with global best practice to ensure safety, security, environmental, quality requirements of the most rigid international IFSA standards what guarantees that product quality is maintained at all times.</p>
      </article>
    </section>

    <section class="page page--right">
      <div class="thumb thumb--fuelling" role="img" aria-label="Fuel truck refuelling an aircraft on the apron"></div>
      <article class="service service--fuelling">
        <h3 class="service__heading">Into-Plane &amp; Ground Fuelling</h3>
        <p class="service__body">We provide our customers with safe, efficient, full scale refuel and defuel of all types of rotary and fixed-wing aircrafts on apron in accordance with the highest industry standards on Health, Safety and Environment. Our policies and procedures have been developed in accordance with the Aviation Transport Council (ATC) 103 Specification and the Joint Fuel Quality Panel (JFQP) Guidelines for Aviation Fuel Quality Control &amp; Operating Procedures. We also provide into-vehicle, into-generator and other ground refuelling services including all aspects of fuel dispensing and management. As part of a turn-key solution, we provide these services wherever they may be required, including our customers' operational sites.</p>
      </article>

      <div class="thumb thumb--laboratory" role="img" aria-label="Glass laboratory flasks holding fuel samples"></div>
      <article class="service service--laboratory">
        <h3 class="service__heading">Laboratories</h3>
        <p class="service__body">Norvane' fuel test laboratories test diverse fuels for full quality specifications, and follow regulatory standards such as AFTS, IQS, and EPI standards. In-house expertise and analytical resources support our operations and guarantees Norvane' customers full integrity of the products and highest quality product.. Norvane own fuel laboratories operate at world-class standards all over the region, supporting our operations from refinery, pipeline, terminal, and other operations.</p>
      </article>

      <div class="photo photo--offshore-rig" role="img" aria-label="Offshore oil platforms silhouetted against a sunset sea"></div>
      <header class="offer-band">
        <h2 class="offer-band__title">WHAT WE OFFER</h2>
        <p class="offer-band__subtitle">Fuel Distribution Logistics &amp; Services</p>
      </header>
    </section>
  </main>
</body>
</html>
```